Real Estate investment company needs billboard designs

This is our website: https://brightlanepropertygroup.com/
We are looking for some billboard concepts that uses our CEO in the design. I have attached some images and 1 billboard design that someone in our industry uses, but we don't want it exactly like his.

Industry/Entity Type

real estate

Colors

Designer to choose colors to be used in the design.

Requirements
Must have
• Company colors from websiute

```html
<!DOCTYPE html>
<html lang="en">
<head>
<meta charset="utf-8">
<title>Bright Lane Property Group – Billboard</title>
<link href="https://fonts.googleapis.com/css2?family=Bebas+Neue&family=Poppins:wght@600;700&display=swap" rel="stylesheet">
<style>
  :root {
    --stage: #8c8c8c;
    --brand-red: #f01818;
    --brand-navy: #1f2143;
    --panel-white: #f6f6f6;
    --text-white: #ffffff;
    --portrait-tone: #2a2a30;
  }
  * { box-sizing: border-box; margin: 0; padding: 0; }
  html, body {
    width: 823px; height: 1200px; overflow: hidden;
    background: var(--stage);
  }
  .billboard {
    position: absolute;
    left: 64px; top: 754px;
    width: 695px; height: 322px;
    background: var(--panel-white);
    box-shadow: 0 6px 18px rgba(0,0,0,0.35);
    overflow: hidden;
  }
  .billboard-art {
    position: absolute; inset: 0;
    width: 695px; height: 322px;
  }
  .brand-name {
    position: absolute;
    left: 392px; width: 274px; top: 30px;
    text-align: center;
    font-family: "Poppins", sans-serif;
    font-weight: 700;
    font-size: 21px;
    line-height: 1.2;
    color: var(--brand-navy);
    text-transform: uppercase;
  }
  .headline {
    position: absolute;
    left: 388px; width: 282px;
    text-align: center;
    font-family: "Bebas Neue", sans-serif;
    font-weight: 400;
    font-size: 76px;
    line-height: 1;
    white-space: nowrap;
  }
  .headline--offer { top: 88px; color: var(--brand-red); }
  .headline--day { top: 151px; color: var(--brand-navy); }
  .subline {
    position: absolute;
    left: 388px; width: 282px; top: 222px;
    text-align: center;
    font-family: "Poppins", sans-serif;
    font-weight: 700;
    font-size: 21px;
    line-height: 1.2;
    color: var(--brand-navy);
    white-space: nowrap;
  }
  .contact-band {
    position: absolute;
    left: 0; right: 0; bottom: 0; height: 63px;
    font-family: "Poppins", sans-serif;
    font-weight: 600;
    color: var(--text-white);
    white-space: nowrap;
  }
  .contact-phone {
    position: absolute; left: 27px; top: 6px;
    font-size: 33px; letter-spacing: 1px; line-height: 1.2;
  }
  .contact-web {
    position: absolute; left: 317px; top: 12px;
    font-size: 22.5px; line-height: 1.2;
  }
</style>
</head>
<body>
  <main class="billboard">
    <svg class="billboard-art" viewBox="0 0 695 322">
      <defs>
        <linearGradient id="sceneTones" x1="0" y1="0" x2="0" y2="1">
          <stop offset="0" stop-color="#5f9a4a"/>
          <stop offset="0.25" stop-color="#3f7a34"/>
          <stop offset="0.45" stop-color="#858b98"/>
          <stop offset="0.62" stop-color="#d9dde0"/>
          <stop offset="0.72" stop-color="#7fb53e"/>
          <stop offset="1" stop-color="#8cc63f"/>
        </linearGradient>
      </defs>
      <g role="img" aria-label="Photo of a grey-roofed suburban house with trees and a green lawn">
        <polygon points="0,0 402,0 334,259 0,259" fill="url(#sceneTones)"/>
      </g>
      <g role="img" aria-label="Photo of the CEO in a black jacket, standing with arms spread wide">
        <rect x="139" y="95" width="203" height="164" rx="10" fill="var(--portrait-tone)"/>
      </g>
      <polygon class="accent-stripe" points="394,0 404,0 336,259 326,259" fill="var(--brand-navy)"/>
      <rect class="contact-fill" x="0" y="259" width="695" height="63" fill="var(--brand-red)"/>
    </svg>

    <div class="brand-name">Bright Lane<br>Property Group</div>
    <h1 class="headline headline--offer">CA$H OFFER</h1>
    <h2 class="headline headline--day">ON SAME DAY</h2>
    <p class="subline">ON SELLING YOUR HOME</p>

    <div class="contact-band">
      <span class="contact-phone">865-555-0142</span>
      <span class="contact-web">brightlanepropertygroup.com</span>
    </div>
  </main>
</body>
</html>
```